Business Card for beauty technology startup

Design Glimora Business Card for a Beauty, based on the website identity and colors (https://www.glimora-example.com).
Glimora is a beauty tech startup that gathers helpful product info for beauty lovers and consumers (such as availability on stores, price range and product reviews) for makeup products. The card design must be young, colorful but clean, and very modern.

Target Market(s)

woman, 15-35

Industry/Entity Type

Cosmetics

Contact Information for Business Card

Full Name, address, phone

Font styles to use
Other font styles liked:
• Advent Pro

Colors
e34297
86cfc6
ffffff
5c5c5c
e8e8e8
e667a6
b2b2b2

Requirements
Must have
• One full colored side with a creative design and another with card info
• Use Color palette: #95C5C5 and/or #D38AA5
• Use fonts: Advent Pro
• Use website identity: https://www.glimora-example.com
Nice to have
• If needed extra font: Roboto

```html
<!DOCTYPE html>
<html lang="en">
<head>
<meta charset="utf-8">
<title>Glimora Business Card</title>
<link href="https://fonts.googleapis.com/css2?family=Advent+Pro:wght@300;400&family=Roboto+Condensed:wght@400;500&family=Roboto:wght@400&display=swap" rel="stylesheet">
<style>
  :root {
    --backdrop: #2b2b2b;
    --card-white: #f4f4f4;
    --rose: #b87f93;
    --rose-soft: #c596a8;
    --ink: #555555;
    --ink-dark: #444444;
    --rule: #b2b2b2;
    --strip: #a9a9a9;
    --white: #ffffff;
  }
  * { box-sizing: border-box; margin: 0; padding: 0; }
  html, body { width: 1200px; height: 960px; overflow: hidden; }
  body { background: var(--backdrop); position: relative; font-family: "Roboto", Arial, sans-serif; }

  .card { position: absolute; width: 600px; height: 342px; border-radius: 18px; overflow: hidden; }

  /* Front side */
  .card-front { left: 314px; top: 113px; background: var(--card-white); }
  .brand-block { position: absolute; left: 60px; top: 75px; width: 236px; text-align: center; }
  .brand-dot { display: block; margin: 0 auto 26px; width: 96px; height: 96px; border: 3px solid var(--rose); border-radius: 50%; }
  .brand-name { font-family: "Advent Pro", sans-serif; font-weight: 300; font-size: 42px; letter-spacing: 7px; color: var(--rose); line-height: 1; }
  .divider { position: absolute; left: 303px; top: 62px; width: 2px; height: 200px; background: linear-gradient(to bottom, transparent, var(--rule) 20%, var(--rule) 80%, transparent); }
  .contact { position: absolute; left: 340px; top: 66px; color: var(--ink); }
  .person-name { font-family: "Roboto Condensed", sans-serif; font-weight: 500; font-size: 21px; color: var(--rose); line-height: 1.2; }
  .person-role { font-family: "Roboto Condensed", sans-serif; font-size: 15px; color: var(--ink-dark); margin-top: 3px; }
  .address { font-size: 14.5px; line-height: 19px; margin-top: 12px; }
  .contact-list { list-style: none; margin-top: 9px; font-size: 14.5px; }
  .contact-list li { display: flex; align-items: center; height: 19px; }
  .contact-list svg { width: 14px; height: 14px; margin-right: 9px; fill: var(--rose); }
  .front-strip { position: absolute; left: 0; bottom: 0; width: 600px; height: 12px; background: var(--strip); }
  .front-band { position: absolute; right: 0; bottom: 0; width: 290px; height: 42px; background: var(--rose); clip-path: polygon(42px 0, 100% 0, 100% 100%, 0 100%); }
  .front-url { position: absolute; right: 40px; bottom: 12px; font-size: 13px; letter-spacing: 1.6px; color: var(--white); white-space: nowrap; }

  /* Back side */
  .card-back { left: 311px; top: 472px; background: var(--rose); }
  .back-ring { position: absolute; left: 10px; top: 10px; width: 320px; height: 320px; border: 6px solid var(--rose-soft); border-radius: 50%; }
  .back-brand { position: absolute; right: 32px; top: 246px; text-align: right; color: var(--white); }
  .back-name { font-family: "Advent Pro", sans-serif; font-weight: 300; font-size: 52px; letter-spacing: 6px; line-height: 1; }
  .back-url { font-size: 14px; letter-spacing: 2.5px; margin-top: 6px; white-space: nowrap; }
</style>
</head>
<body>
  <section class="card card-front">
    <div class="brand-block">
      <span class="brand-dot"></span>
      <div class="brand-name">GLIMORA</div>
    </div>
    <div class="divider"></div>
    <div class="contact">
      <div class="person-name">MARA LINDQVIST</div>
      <div class="person-role">CEO/FOUNDER</div>
      <div class="address">214 Willowbend Court<br>Fairview, Oregon 97024</div>
      <ul class="contact-list">
        <li><svg viewBox="0 0 24 24"><path d="M6.6 10.8a15 15 0 0 0 6.6 6.6l2.2-2.2a1 1 0 0 1 1-.25 11.4 11.4 0 0 0 3.6.57 1 1 0 0 1 1 1V20a1 1 0 0 1-1 1A17 17 0 0 1 3 4a1 1 0 0 1 1-1h3.5a1 1 0 0 1 1 1c0 1.25.2 2.450.57 3.6a1 1 0 0 1-.25 1z"/></svg>555 210 4837</li>
        <li><svg viewBox="0 0 24 24"><path d="M7 1h10a2 2 0 0 1 2 2v18a2 2 0 0 1-2 2H7a2 2 0 0 1-2-2V3a2 2 0 0 1 2-2zm0 3v14h10V4zm5 15.5a1.2 1.2 0 1 0 0 2.4 1.2 1.2 0 0 0 0-2.4z"/></svg>555 318 6042</li>
        <li><svg viewBox="0 0 24 24"><path d="M6 2h12v6H6zM3 9h18a1 1 0 0 1 1 1v8h-4v4H6v-4H2v-8a1 1 0 0 1 1-1zm5 7v4h8v-4z"/></svg>555 472 9153</li>
        <li><svg viewBox="0 0 24 24"><path d="M2 5h20v14H2zm2 2v.5l8 5 8-5V7z"/></svg>info@glimora-example.com</li>
      </ul>
    </div>
    <div class="front-strip"></div>
    <div class="front-band"></div>
    <div class="front-url">www.glimora-example.com</div>
  </section>

  <section class="card card-back">
    <div class="back-ring"></div>
    <div class="back-brand">
      <div class="back-name">GLIMORA</div>
      <div class="back-url">www.glimora-example.com</div>
    </div>
  </section>
</body>
</html>
```